Ecard for facebook and Instagram postings

I need 4 ecards (don't know if that is what it is called) for Facebook and Instagram postings. My Logo and company name should be incorporated and also be square. I would like to be able to insert text as I need. Examples are:

https://www.plorvexa.com/photo.php?fbid=20262841672382489&set=a.20261729249182489.516031.71298967488&type=1&relevant_count=1

https://media-a-kpt.yy.plorvexacdn.net/hpics-bmk4/2345967_657092986477056_308792573_n.jpg

I don't necessarily need images on them, just the color scheme to my business cards and the logo and business name. But if you'd like to give it an interesting look, you can go ahead and play with it. My site is tornquillmentoring.com, if you'd like to see the style of it.

Thank you!!!
Updates

I just uploaded the logo in two variations.  Thank you!

Target Market(s)

Women 16-65

Industry/Entity Type

Business

Requirements
Must have
• Logo and business name
Should not have
• No white background. I have attached business card picture so you can have an idea of what I'd like.

```html
<!DOCTYPE html>
<html lang="en">
<head>
<meta charset="utf-8">
<title>Tornquill Mentoring Services – Quote Card</title>
<link rel="stylesheet" href="https://fonts.googleapis.com/css2?family=Tinos:wght@700&display=swap">
<style>
  :root {
    --orange-light: #f7962f;
    --orange-mid: #f08224;
    --orange-deep: #e86d17;
    --orange-band: #ef7e22;
    --crimson: #c21f3a;
    --ink: #111111;
    --white: #ffffff;
  }
  html, body {
    margin: 0;
    padding: 0;
    width: 1200px;
    height: 1200px;
    overflow: hidden;
    background: var(--orange-mid);
  }
  .card {
    position: relative;
    width: 1200px;
    height: 1200px;
    overflow: hidden;
    background: radial-gradient(ellipse at 50% 45%, var(--orange-light) 0%, var(--orange-mid) 55%, var(--orange-deep) 100%);
    font-family: "Tinos", "Times New Roman", serif;
  }
  .card__top-edge {
    position: absolute;
    inset: 0 0 auto 0;
    height: 12px;
    background: var(--orange-light);
  }
  .card__swoosh {
    position: absolute;
    inset: 0;
    width: 1200px;
    height: 1200px;
  }
  .quote-mark {
    position: absolute;
    margin: 0;
    color: var(--crimson);
    font-weight: 700;
    font-size: 330px;
    line-height: 1;
  }
  .quote-mark--open { left: 50px; top: 40px; }
  .quote-mark--close { left: 950px; top: 780px; }
  .quote {
    position: absolute;
    left: 0;
    right: 0;
    top: 222px;
    margin: 0;
    text-align: center;
    color: var(--ink);
    font-weight: 700;
    font-size: 104px;
    line-height: 130px;
  }
  .brand {
    position: absolute;
    left: 28px;
    top: 1030px;
    color: var(--white);
    font-weight: 700;
  }
  .brand__name {
    display: block;
    font-size: 74px;
    line-height: 1;
  }
  .brand__tagline {
    display: block;
    margin-top: 18px;
    font-size: 27px;
    letter-spacing: 7px;
    text-transform: uppercase;
  }
  .brand-mark {
    position: absolute;
    left: 1020px;
    top: 1053px;
    width: 110px;
    height: 110px;
    border-radius: 50%;
    background: var(--white);
    box-shadow: 0 0 0 5px var(--orange-band);
  }
</style>
</head>
<body>
  <main class="card">
    <div class="card__top-edge"></div>

    <svg class="card__swoosh" viewBox="0 0 1200 1200" aria-hidden="true">
      <path d="M0 972 Q420 915 1200 1062 L1200 1200 L0 1200 Z" fill="var(--crimson)"/>
      <path d="M0 986 Q500 950 1200 1148 L1200 1180 L0 1180 Z" fill="var(--orange-band)"/>
    </svg>

    <p class="quote-mark quote-mark--open" aria-hidden="true">&ldquo;</p>

    <blockquote class="quote">
      Ignorance is the<br>
      curse of God;<br>
      knowledge is the<br>
      wing wherewith we<br>
      fly to heaven
    </blockquote>

    <p class="quote-mark quote-mark--close" aria-hidden="true">&rdquo;</p>

    <div class="brand">
      <span class="brand__name">Tornquill</span>
      <span class="brand__tagline">Mentoring Services</span>
    </div>

    <div class="brand-mark" aria-hidden="true"></div>
  </main>
</body>
</html>
```